Create a Creative Shopify banner for a Streetwear Brand

We need a banner for our brand Velto Studios explaining the meaning of our brand we want the banner to be a simple professional looking design of a wizard/sage/magi looking up at the stars looking at a big four pointed star. we want the design to be black and white. and have this text in a aesthetic font underneath it.
"Velto Studios is a spiritually inspired streetwear brand that fuses modern aesthetics with sacred symbols and cosmic motifs. Drawing inspiration from the Magi—wise sages who followed the stars in search of enlightenment—our designs serve as a reminder that the universe is always guiding us."
we want it to match the stars from the ai file of our brand banner I put in the files. I also put a simple drawing I made and some pictures of wizards into the files as a reference. here is our website for reference velto-studios.com

```html
<!DOCTYPE html>
<html lang="en">
<head>
<meta charset="utf-8">
<title>Velto Studios Story Banner</title>
<link href="https://fonts.googleapis.com/css2?family=Fraunces:opsz,wght@9..144,600&family=Quicksand:wght@500&family=Almendra:wght@700&family=Dancing+Script:wght@700&display=swap" rel="stylesheet">
<style>
  :root {
    --ink: #000000;
    --night-deep: #050505;
    --night-mid: #1c1c1c;
    --wood-dark: #0d0d0d;
    --wood-mid: #2e2e2e;
    --figure-light: #8a8a8a;
    --figure-dark: #1a1a1a;
    --paper: #ffffff;
  }
  * { margin: 0; padding: 0; box-sizing: border-box; }
  html, body { width: 797px; height: 1200px; overflow: hidden; background: var(--ink); }
  .banner {
    position: relative;
    width: 797px;
    height: 1200px;
    overflow: hidden;
    background: var(--wood-dark);
    color: var(--paper);
  }
  .night-sky {
    position: absolute;
    inset: 0 0 auto 0;
    height: 640px;
    background:
      radial-gradient(ellipse 240px 200px at 92% 14%, rgba(160,160,160,.55), transparent 70%),
      radial-gradient(ellipse 200px 150px at 18% 6%, rgba(120,120,120,.45), transparent 70%),
      radial-gradient(ellipse 300px 150px at 42% 40%, rgba(95,95,95,.45), transparent 70%),
      radial-gradient(ellipse 220px 120px at 14% 55%, rgba(80,80,80,.4), transparent 70%),
      linear-gradient(180deg, var(--night-mid) 0%, #191919 50%, var(--night-deep) 100%);
  }
  .star-field {
    position: absolute;
    left: 0; top: 0;
    width: 797px; height: 600px;
  }
  .wizard-figure {
    position: absolute;
    left: 350px; top: 302px;
    width: 240px; height: 318px;
    border-radius: 120px 120px 20px 20px;
    background: radial-gradient(ellipse at 50% 35%, var(--figure-light), var(--figure-dark) 75%);
  }
  .wood-panel {
    position: absolute;
    inset: 630px 0 0 0;
    background:
      radial-gradient(ellipse 420px 300px at 50% 45%, rgba(70,70,70,.55), transparent 75%),
      linear-gradient(180deg, var(--wood-mid) 0%, var(--wood-dark) 100%);
  }
  .horizon {
    position: absolute;
    left: 0; top: 596px;
    width: 797px; height: 50px;
  }
  .brand-name {
    position: absolute;
    top: 52px; left: 0; width: 100%;
    text-align: center;
    font-family: "Fraunces", Georgia, serif;
    font-weight: 600;
    font-size: 46px;
    line-height: 1;
    color: var(--paper);
  }
  .tagline {
    position: absolute;
    top: 139px; left: 0; width: 100%;
    text-align: center;
    font-family: "Quicksand", Arial, sans-serif;
    font-weight: 500;
    font-size: 20px;
    color: var(--paper);
  }
  .headline {
    position: absolute;
    top: 176px; left: 0; width: 100%;
    text-align: center;
    font-family: "Fraunces", Georgia, serif;
    font-weight: 600;
    font-size: 43px;
    letter-spacing: -1px;
    line-height: 1.1;
    color: var(--paper);
  }
  .brand-story {
    position: absolute;
    top: 676px; left: 66px;
    width: 666px;
    font-family: "Almendra", Georgia, serif;
    font-weight: 700;
    font-size: 33px;
    line-height: 48.5px;
    text-align: justify;
    color: var(--paper);
  }
  .story-title {
    position: absolute;
    top: 1098px; right: 64px;
    font-family: "Dancing Script", cursive;
    font-weight: 700;
    font-size: 52px;
    line-height: 1.2;
    color: var(--paper);
  }
</style>
</head>
<body>
<main class="banner">
  <div class="night-sky" role="img" aria-label="Black and white night sky with soft clouds"></div>

  <svg class="star-field" viewBox="0 0 797 600" aria-hidden="true">
    <defs>
      <path id="sparkle" d="M0 -6 L1.2 -1.2 L6 0 L1.2 1.2 L0 6 L-1.2 1.2 L-6 0 L-1.2 -1.2 Z" fill="var(--paper)"/>
    </defs>
    <g>
      <use href="#sparkle" x="20" y="24"/><use href="#sparkle" x="76" y="46"/><use href="#sparkle" x="45" y="88"/>
      <use href="#sparkle" x="104" y="113"/><use href="#sparkle" x="28" y="150"/><use href="#sparkle" x="78" y="165"/>
      <use href="#sparkle" x="158" y="166"/><use href="#sparkle" x="180" y="120"/><use href="#sparkle" x="222" y="57"/>
      <use href="#sparkle" x="233" y="8"/><use href="#sparkle" x="278" y="95"/><use href="#sparkle" x="572" y="10"/>
      <use href="#sparkle" x="572" y="52"/><use href="#sparkle" x="624" y="76"/><use href="#sparkle" x="554" y="124"/>
      <use href="#sparkle" x="692" y="38"/><use href="#sparkle" x="738" y="52"/><use href="#sparkle" x="764" y="102"/>
      <use href="#sparkle" x="648" y="142"/><use href="#sparkle" x="718" y="152"/><use href="#sparkle" x="600" y="168"/>
      <use href="#sparkle" x="775" y="180"/><use href="#sparkle" x="764" y="242"/><use href="#sparkle" x="714" y="268"/>
      <use href="#sparkle" x="652" y="306"/><use href="#sparkle" x="586" y="300"/><use href="#sparkle" x="490" y="265"/>
      <use href="#sparkle" x="432" y="297"/><use href="#sparkle" x="305" y="300"/><use href="#sparkle" x="211" y="261"/>
      <use href="#sparkle" x="144" y="258"/><use href="#sparkle" x="66" y="250"/><use href="#sparkle" x="84" y="294"/>
      <use href="#sparkle" x="31" y="321"/><use href="#sparkle" x="142" y="354"/><use href="#sparkle" x="192" y="337"/>
      <use href="#sparkle" x="95" y="352"/><use href="#sparkle" x="21" y="382"/><use href="#sparkle" x="78" y="411"/>
      <use href="#sparkle" x="148" y="421"/><use href="#sparkle" x="243" y="439"/><use href="#sparkle" x="306" y="494"/>
      <use href="#sparkle" x="173" y="484"/><use href="#sparkle" x="59" y="511"/><use href="#sparkle" x="105" y="525"/>
      <use href="#sparkle" x="224" y="510"/><use href="#sparkle" x="175" y="537"/><use href="#sparkle" x="14" y="549"/>
      <use href="#sparkle" x="226" y="556"/><use href="#sparkle" x="383" y="520"/><use href="#sparkle" x="328" y="551"/>
      <use href="#sparkle" x="617" y="444"/><use href="#sparkle" x="693" y="449"/><use href="#sparkle" x="752" y="475"/>
      <use href="#sparkle" x="634" y="536"/><use href="#sparkle" x="720" y="518"/><use href="#sparkle" x="776" y="538"/>
      <use href="#sparkle" x="680" y="555"/><use href="#sparkle" x="614" y="352"/><use href="#sparkle" x="684" y="344"/>
      <use href="#sparkle" x="768" y="412"/><use href="#sparkle" x="720" y="397"/><use href="#sparkle" x="28" y="227"/>
    </g>
    <g class="guiding-star" transform="translate(249 285)">
      <path d="M0 -30 C3 -8 8 -3 30 0 C8 3 3 8 0 30 C-3 8 -8 3 -30 0 C-8 -3 -3 -8 0 -30 Z" fill="var(--paper)"/>
      <circle r="9" fill="var(--paper)" opacity=".6"/>
      <path d="M0 -56 V-44 M0 44 V56 M-56 0 H-44 M44 0 H56 M-28 -28 L-20 -20 M20 20 L28 28 M28 -28 L20 -20 M-20 20 L-28 28" stroke="var(--paper)" stroke-width="1" opacity=".8"/>
    </g>
  </svg>

  <div class="wizard-figure" role="img" aria-label="Bearded wizard in a pointed hat and flowing cloak holding a star-topped staff, gazing up at the guiding star"></div>

  <div class="wood-panel" role="img" aria-label="Dark wood-grain texture background"></div>

  <svg class="horizon" viewBox="0 0 797 50" aria-hidden="true">
    <path d="M0 38 C180 30 360 12 500 10 C620 10 720 28 797 44 L797 50 C700 40 600 34 480 34 C340 34 170 42 0 44 Z" fill="var(--paper)"/>
  </svg>

  <div class="brand-name">Velto Studios</div>
  <p class="tagline">spiritually inspired streetwear</p>
  <h1 class="headline">Clothing for the Mysticallly inclined</h1>

  <p class="brand-story">Velto Studios is a spiritually inspired streetwear brand that fuses modern aesthetics with sacred symbols and cosmic motifs. Drawing inspiration from the Magi—wise sages who followed the stars in search of enlightenment. Our designs serve as a reminder that the universe is always guiding us.</p>

  <p class="story-title">Velto Studios Story</p>
</main>
</body>
</html>
```